Non Profit Company Looking For New Website

The website for Fernvale Quillstone Heritage Society should offer the viewer beautiful photos that inspire condifence and joy and tap into our love of horses.

We would like to see a website that displays trust, quality and confidence. Needs to be responsive and mobile friendly for all browsers and coded for both Android & IOS.

READ ATTACHED WEBSITE TEMPLATE FOR COMPLETE DETAILS ON WHAT WE ARE LOOKING FOR.

Looking for recommmendations if we should use WordPress/WooCommerce for site or Wordpress with Shopify Plug in or just Shopify.

Must be both desktop and mobile friendly with fast page load speed. Need the ability to edit ourselves.

Industry/Entity Type

Non Profit

Coding

Coded - Design and coding required

Number of Pages Required

5+ page

Requirements
Must have
• We would like to see a website that displays trust, quality and confidence. Needs to be responsive and mobile friendly for all browsers and coded for both Android & IOS.

Looking for recommendations if we should use WordPress/WooCommerce for site or Wordpress with Shopify Plug in or just Shopify.

Logo Colour:
Pantone 7621 C

READ TEMPLATE THAT IS ATTACHED
Nice to have
• Like look of this website as a sample:
https://www.quellbrimtorva.com/

Another similar non profit organization
https://pellaworthcindle.com/

```html
<!DOCTYPE html>
<html lang="en">
<head>
<meta charset="utf-8">
<title>Fernvale Presentation</title>
<link href="https://fonts.googleapis.com/css2?family=Prata&family=Mulish:wght@400;600&family=Roboto:wght@500;700;900&display=swap" rel="stylesheet">
<style>
:root{
  --red:#b81c2c;
  --red-deep:#a0172a;
  --white:#ffffff;
  --ink:#111111;
  --black:#000000;
  --dark:#1f1f1f;
  --stage:#242424;
  --grey:#5e5e5e;
  --serif:'Prata', Georgia, serif;
  --sans:'Mulish', Arial, sans-serif;
  --display:'Roboto', Arial, sans-serif;
}
*{box-sizing:border-box;margin:0;padding:0}
html,body{width:1200px;height:3870px;overflow:hidden}
body{position:relative;background:var(--dark);font-family:var(--sans);color:var(--white)}
.abs{position:absolute}
.stage-top{left:0;top:0;width:1200px;height:1265px;background:radial-gradient(ellipse at 60% 40%,#333 0%,var(--stage) 70%)}
.photo{position:absolute}
.btn{position:absolute;background:var(--white);color:var(--ink);font-family:var(--serif);text-transform:uppercase;text-align:center;letter-spacing:.5px}

/* presentation titles */
.board-title{left:360px;width:480px;text-align:center;font-family:var(--display);font-weight:700;line-height:1}
.vertical-label{left:362px;font-family:var(--display);font-weight:700;font-size:46px;line-height:66px;width:40px;text-align:center}

/* mobile page */
.mobile{left:78px;top:8px;width:258px;height:3780px;background:var(--white);overflow:hidden}
.m-head{left:0;top:0;width:258px;height:90px;background:var(--white)}
.brand{font-family:var(--serif);color:var(--red);line-height:1.1}
.burger{right:14px;top:36px;width:30px;height:20px;border-top:3px solid var(--ink);border-bottom:3px solid var(--ink)}
.burger::after{content:"";position:absolute;left:0;top:6px;width:30px;height:3px;background:var(--ink)}
.m-text{font-size:14px;line-height:1.55}
.serif-h{font-family:var(--serif);font-weight:400}

/* desktop page */
.desk{left:552px;top:1842px;width:411px;height:1290px;background:var(--white);overflow:hidden}
.d-small{font-size:6px;line-height:1.5}
.d-nav span{margin-left:12px;font-size:5px;color:var(--ink);text-transform:uppercase}
.d-field{position:absolute;height:12px;background:var(--white);font-size:5px;color:#777;padding:2px 4px}

.swatch{top:1545px;width:74px;height:74px;border-radius:50%}
.sw-label{top:1632px;font-family:var(--display);font-weight:500;font-size:22px;width:110px;text-align:center}
</style>
</head>
<body>

<div class="abs stage-top"></div>

<!-- presentation headings -->
<div class="abs board-title" style="top:22px;font-size:48px;font-weight:700">FERNVALE</div>
<div class="abs board-title" style="top:70px;font-size:66px;font-weight:900">PRESENTATION</div>
<div class="abs vertical-label" style="top:352px">M<br>O<br>B<br>I<br>L<br>E</div>
<div class="abs vertical-label" style="top:880px">V<br>I<br>E<br>W</div>

<!-- flat hero screen -->
<section class="abs" style="left:500px;top:160px;width:560px;height:380px;background:var(--white)" aria-label="Desktop hero screen">
  <div class="photo" role="img" aria-label="Photo of a dark horse in a halter on green grass" style="left:0;top:30px;width:560px;height:350px;background:linear-gradient(120deg,#dcdcd6 0%,#8a8f84 35%,#2a2a26 55%,#6f9a3c 100%)"></div>
  <div class="brand abs" style="left:20px;top:8px;font-size:11px">Fernvale Quillstone</div>
  <div class="abs" style="left:300px;top:60px;width:230px;height:200px;background:var(--red)">
    <div class="serif-h" style="margin:40px 20px 0;font-size:24px;line-height:1.2;text-align:center">We Support<br>And Develop</div>
    <div class="serif-h" style="margin:8px 20px;font-size:12px;text-align:center">retired thoroughbred racehorses<br>for their next chapter in life</div>
    <div class="btn" style="left:75px;top:165px;width:80px;font-size:8px;padding:3px 0">View horses</div>
  </div>
</section>
<section class="abs" style="left:540px;top:620px;width:480px;height:300px;background:var(--white)" aria-label="Laptop hero screen">
  <div class="photo" role="img" aria-label="Photo of a dark horse in a halter outdoors" style="left:0;top:24px;width:480px;height:276px;background:linear-gradient(120deg,#dcdcd6 0%,#8a8f84 35%,#2a2a26 55%,#6f9a3c 100%)"></div>
  <div class="brand abs" style="left:16px;top:6px;font-size:10px">Fernvale Quillstone</div>
  <div class="abs" style="left:250px;top:50px;width:190px;height:160px;background:var(--red)">
    <div class="serif-h" style="margin:32px 14px 0;font-size:20px;line-height:1.2;text-align:center">We Support<br>And Develop</div>
    <div class="serif-h" style="margin:6px 14px;font-size:10px;text-align:center">retired thoroughbred racehorses for their next chapter in life</div>
  </div>
</section>

<!-- ================= MOBILE VIEW ================= -->
<main class="abs mobile">
  <header class="abs m-head">
    <div class="brand abs" style="left:14px;top:26px;font-size:10px;width:70px;text-align:center">FERNVALE<br>QUILLSTONE</div>
    <div class="abs burger"></div>
  </header>

  <section class="abs" style="left:0;top:90px;width:258px;height:217px;background:var(--white)">
    <div class="photo" role="img" aria-label="Photo of a dark horse with a rope halter" style="left:0;top:0;width:258px;height:172px;background:linear-gradient(110deg,#d9d9d2 0%,#6d6d64 30%,#262622 55%,#7da54a 100%)"></div>
    <div class="abs" style="left:70px;top:172px;width:188px;height:45px;background:var(--red)"></div>
    <div class="abs" style="left:132px;top:22px;width:126px;height:173px;background:var(--red);text-align:center">
      <div class="serif-h" style="margin-top:12px;font-size:15px;line-height:1.25">We Support<br>And Develop</div>
      <div class="serif-h" style="font-size:11.5px;line-height:1.4;margin-top:4px">retired thorough<br>bred<br>racehorses<br>for their<br>next chapter in life</div>
    </div>
    <div class="btn" style="left:132px;top:180px;width:118px;font-size:11px;padding:3px 0">View horses</div>
  </section>

  <section class="abs" style="left:0;top:307px;width:258px;height:353px;background:var(--white);text-align:center">
    <div class="photo" role="img" aria-label="Illustration of a grey horse and a young rider beside a large red letter" style="left:50px;top:30px;width:160px;height:160px;background:radial-gradient(circle at 50% 55%,#d63a48 0%,#e9e2dd 55%,var(--white) 75%)"></div>
    <div class="abs serif-h" style="left:0;top:134px;width:258px;font-size:13px;color:var(--red);font-style:italic">Retire. Retrain. Rehome.</div>
    <p class="abs m-text" style="left:30px;top:208px;width:198px;color:#444;font-size:14.5px;line-height:1.55">Fernvale Quillstone Heritage Society (FQHS) is a registered not-for-profit organization in Fernvale.</p>
  </section>

  <section class="abs" style="left:0;top:660px;width:258px;height:462px;background:linear-gradient(180deg,var(--red) 0%,#c22535 100%)">
    <div class="photo" role="img" aria-label="Round photo of two horses nuzzling" style="left:54px;top:8px;width:158px;height:158px;border-radius:50%;background:radial-gradient(circle at 45% 45%,#8a5a3a 0%,#3b2518 55%,#9fb06a 100%)"></div>
    <h2 class="abs serif-h" style="left:9px;top:168px;font-size:21px;line-height:1.5">What is<br>Thoroughbred<br>Aftercare?</h2>
    <p class="abs m-text" style="left:9px;top:268px;width:240px">The health, safety and welfare of our equine athletes does not end at the finish line, and retirement and aftercare are critical to the success of the racing industry.</p>
    <div class="btn" style="left:9px;top:413px;width:172px;font-size:11px;padding:3px 0">Learn more about us</div>
  </section>

  <section class="abs" style="left:0;top:1122px;width:258px;height:453px;background:linear-gradient(180deg,#2a2a2a 0%,#171717 100%)">
    <h2 class="abs serif-h" style="left:9px;top:40px;font-size:21px">Adopt a Horse</h2>
    <p class="abs m-text" style="left:9px;top:88px;width:245px;font-size:14px;line-height:1.5">Fernvale Quillstone Heritage is committed to helping match you with the perfect horse.</p>
    <div class="photo" role="img" aria-label="Photo of a bay horse standing in a paddock" style="left:36px;top:175px;width:194px;height:178px;border:2px solid var(--red);background:linear-gradient(180deg,#cfd6e0 0%,#8fa08a 45%,#5a3a26 60%,#9a9a88 100%)"></div>
    <svg class="abs" style="left:7px;top:248px" width="28" height="28" viewBox="0 0 28 28"><circle cx="14" cy="14" r="13" fill="#fff"/><path d="M16 8 L10 14 L16 20" stroke="#111" stroke-width="3" fill="none"/></svg>
    <svg class="abs" style="left:222px;top:248px" width="28" height="28" viewBox="0 0 28 28"><circle cx="14" cy="14" r="13" fill="#fff"/><path d="M12 8 L18 14 L12 20" stroke="#111" stroke-width="3" fill="none"/></svg>
    <div class="btn" style="left:64px;top:367px;width:134px;font-size:11px;padding:2px 0">Adopt now</div>
  </section>

  <section class="abs" style="left:0;top:1575px;width:258px;height:495px;background:var(--white)">
    <div class="photo" role="img" aria-label="Photo of a bay horse with a white blaze in a red halter" style="left:8px;top:16px;width:242px;height:200px;background:linear-gradient(180deg,#bfc7cf 0%,#6a4630 45%,#3a2416 75%,#8c7a66 100%)"></div>
    <div class="abs" style="left:8px;top:216px;width:242px;height:268px;background:var(--red)">
      <h2 class="serif-h" style="margin:30px 0 0 12px;font-size:20px">Horses</h2>
      <p class="m-text" style="margin:4px 12px 0;font-size:14px">Many desktop publishing packages and web page editors now use Lorem Ipsum as their default model text, and a search for 'lorem ipsum'</p>
      <div class="btn" style="left:12px;top:200px;width:150px;font-size:11px;padding:2px 0">More ways to give</div>
    </div>
  </section>

  <section class="abs" style="left:0;top:2070px;width:258px;height:622px;background:linear-gradient(180deg,var(--red) 0%,#c7303e 100%)">
    <h2 class="abs serif-h" style="left:6px;top:28px;font-size:20px;line-height:1.5;width:260px">Have A Question Or<br>Need More Information</h2>
    <svg class="abs" style="left:8px;top:112px" width="24" height="24" viewBox="0 0 24 24"><circle cx="12" cy="12" r="11" fill="none" stroke="#fff" stroke-width="1.5"/><path d="M12 6a4 4 0 0 0-4 4c0 3 4 8 4 8s4-5 4-8a4 4 0 0 0-4-4z" fill="#fff"/></svg>
    <div class="abs" style="left:48px;top:108px;font-size:15px;font-weight:600">LOCATION</div>
    <div class="abs m-text" style="left:48px;top:128px;font-size:13.5px">Lorem Ipsum is simply<br>Dummy text P.O. Box 156</div>
    <svg class="abs" style="left:8px;top:190px" width="24" height="24" viewBox="0 0 24 24"><circle cx="12" cy="12" r="11" fill="none" stroke="#fff" stroke-width="1.5"/><path d="M8 7l3 0 1 3-2 1a7 7 0 0 0 3 3l1-2 3 1 0 3c-5 0-9-4-9-9z" fill="#fff"/></svg>
    <div class="abs" style="left:48px;top:186px;font-size:15px;font-weight:600">CALL US</div>
    <div class="abs m-text" style="left:48px;top:206px;font-size:13.5px">123-456-789</div>
    <svg class="abs" style="left:8px;top:248px" width="24" height="24" viewBox="0 0 24 24"><circle cx="12" cy="12" r="11" fill="none" stroke="#fff" stroke-width="1.5"/><rect x="6" y="8" width="12" height="8" fill="#fff"/><path d="M6 8l6 5 6-5" stroke="#b81c2c" fill="none"/></svg>
    <div class="abs" style="left:48px;top:244px;font-size:15px;font-weight:600">MAIL US</div>
    <div class="abs m-text" style="left:48px;top:264px;font-size:13.5px">fernvale@mail.com</div>

    <div class="abs m-text" style="left:9px;top:373px;width:240px;height:22px;background:#fff;color:#555;padding:1px 6px">First Name</div>
    <div class="abs m-text" style="left:9px;top:403px;width:240px;height:22px;background:#fff;color:#555;padding:1px 6px">Last Name</div>
    <div class="abs m-text" style="left:9px;top:433px;width:240px;height:22px;background:#fff;color:#555;padding:1px 6px">Phone</div>
    <div class="abs m-text" style="left:9px;top:463px;width:240px;height:22px;background:#fff;color:#555;padding:1px 6px">Email</div>
    <div class="abs m-text" style="left:9px;top:493px;width:240px;height:60px;background:#fff;color:#555;padding:3px 6px">How can we help you?</div>
    <div class="btn" style="left:9px;top:564px;width:128px;font-size:11px;padding:3px 0">Submit now</div>
  </section>

  <footer class="abs" style="left:0;top:2692px;width:258px;height:1088px;background:var(--black)">
    <div class="brand abs" style="left:10px;top:50px;width:150px;text-align:center;font-size:20px">FERNVALE</div>
    <div class="abs" style="left:65px;top:88px;width:38px;height:38px;border-radius:50%;background:var(--red)"></div>
    <div class="brand abs" style="left:10px;top:150px;width:150px;text-align:center;font-size:13px">QUILLSTONE<br>HERITAGE</div>
    <h3 class="abs serif-h" style="left:9px;top:248px;font-size:15px">QUICK LINK</h3>
    <div class="abs m-text" style="left:9px;top:290px;font-size:13.5px;line-height:33px">Home<br>About<br>Adopt<br>Horses<br>Donate / Shop<br>Contact</div>
    <h3 class="abs serif-h" style="left:9px;top:532px;font-size:15px">QUICK CONTACT</h3>
    <div class="abs m-text" style="left:9px;top:580px;font-size:13.5px;line-height:21px"><span style="color:var(--red)">Location</span><br><span style="display:inline-block;margin-top:6px">Lorem Ipsum is simply<br>Dummy text<br>P.O. Box 156</span></div>
    <div class="abs m-text" style="left:9px;top:686px;font-size:13.5px;line-height:21px"><span style="color:var(--red)">Location</span><br><span style="display:inline-block;margin-top:6px">Lorem Ipsum is simply<br>Dummy text<br>P.O. Box 156</span></div>
    <h3 class="abs serif-h" style="left:9px;top:822px;font-size:15px">FOLLOW US</h3>
    <div class="abs m-text" style="left:9px;top:870px;width:226px;height:38px;background:#fff;color:var(--ink);text-align:center;line-height:38px">Enter Your Mail ID</div>
    <div class="abs serif-h" style="left:9px;top:915px;width:226px;height:38px;background:var(--red);text-align:center;line-height:38px;font-size:16px">Subscribe</div>
    <svg class="abs" style="left:18px;top:978px" width="130" height="28" viewBox="0 0 130 28"><circle cx="13" cy="14" r="12" fill="#fff"/><circle cx="48" cy="14" r="12" fill="#fff"/><circle cx="83" cy="14" r="12" fill="#fff"/><circle cx="118" cy="14" r="12" fill="#fff"/></svg>
    <div class="abs" style="left:9px;top:1038px;font-size:12px;line-height:19px;color:#aaa">Copyright 2021 <span style="color:var(--red)">Fernvale</span><br>All Right Reserved</div>
  </footer>
</main>

<!-- ================= TYPE & COLOUR ================= -->
<div class="abs" style="left:500px;top:1330px;width:540px;text-align:center;font-family:var(--display);font-weight:500;font-size:38px">Typography &amp; Colors</div>
<div class="abs" style="left:500px;top:1395px;width:540px;text-align:center;font-family:var(--display);font-weight:700;font-size:60px;letter-spacing:1px">Afterglow &amp; Muli</div>
<div class="abs swatch" style="left:571px;background:var(--red)"></div>
<div class="abs swatch" style="left:683px;background:var(--white)"></div>
<div class="abs swatch" style="left:787px;background:#222"></div>
<div class="abs swatch" style="left:886px;background:var(--black)"></div>
<div class="abs sw-label" style="left:553px">#a0c83d</div>
<div class="abs sw-label" style="left:665px">#4d6908</div>
<div class="abs sw-label" style="left:769px">#092014</div>
<div class="abs sw-label" style="left:868px">#5e5e5e</div>
<div class="abs" style="left:500px;top:1740px;width:530px;text-align:center;font-family:var(--display);font-weight:500;font-size:50px">DESKTOP VIEW</div>

<!-- ================= DESKTOP VIEW ================= -->
<main class="abs desk">
  <header class="abs" style="left:0;top:0;width:411px;height:33px;background:#fff">
    <div class="brand abs" style="left:50px;top:6px;font-size:7px;text-align:center">FERNVALE<br>QUILLSTONE</div>
    <nav class="abs d-nav" style="left:150px;top:12px"><span style="color:var(--red)">Home</span><span>About</span><span>Adopt</span><span>Horses</span><span>Donate / Shop</span><span>Contact</span></nav>
  </header>
  <section class="abs" style="left:0;top:33px;width:411px;height:187px">
    <div class="photo" role="img" aria-label="Photo of a dark horse in a halter on grass" style="left:0;top:0;width:411px;height:187px;background:linear-gradient(110deg,#ddddd6 0%,#75756c 30%,#262622 52%,#76a342 100%)"></div>
    <div class="abs" style="left:208px;top:0;width:203px;height:187px;background:var(--red)"></div>
    <div class="abs" style="left:210px;top:28px;width:150px;height:120px;text-align:center">
      <div class="serif-h" style="font-size:15px;line-height:1.2;margin-top:10px">We Support<br>And Develop</div>
      <div class="serif-h" style="font-size:7.5px;margin-top:4px">retired thoroughbred racehorses<br>for their next chapter in life</div>
      <div class="btn" style="left:45px;top:82px;width:62px;font-size:5px;padding:2px 0">View horses</div>
    </div>
  </section>
  <section class="abs" style="left:0;top:220px;width:411px;height:161px;background:#fff;text-align:center">
    <div class="photo" role="img" aria-label="Illustration of a grey horse and a rider beside a red letter" style="left:145px;top:8px;width:120px;height:96px;background:radial-gradient(circle at 50% 55%,#d63a48 0%,#e9e2dd 55%,#fff 75%)"></div>
    <div class="abs serif-h" style="left:0;top:78px;width:411px;font-size:10px;color:var(--red);font-style:italic">Retire. Retrain. Rehome.</div>
    <div class="abs d-small" style="left:100px;top:118px;width:211px;color:#555">Fernvale Quillstone Heritage Society (FQHS) is a registered not-for-profit organization in Fernvale.</div>
  </section>
  <section class="abs" style="left:0;top:381px;width:411px;height:162px;background:var(--red)">
    <div class="abs serif-h" style="left:54px;top:34px;font-size:10px;line-height:1.3">What is Thoroughbred<br>Aftercare?</div>
    <div class="abs d-small" style="left:54px;top:66px;width:140px;font-size:5px">The health, safety and welfare of our equine athletes does not end at the finish line, and retirement and aftercare are critical to the success of the racing industry.</div>
    <div class="btn" style="left:54px;top:114px;width:78px;font-size:4.5px;padding:2px 0">Learn more about us</div>
    <div class="photo" role="img" aria-label="Round photo of two horses nuzzling" style="left:228px;top:18px;width:130px;height:130px;border-radius:50%;background:radial-gradient(circle at 45% 45%,#8a5a3a 0%,#3b2518 55%,#9fb06a 100%)"></div>
  </section>
  <section class="abs" style="left:0;top:543px;width:411px;height:230px;background:linear-gradient(180deg,#2b2b2b 0%,#171717 100%);text-align:center">
    <div class="abs serif-h" style="left:0;top:26px;width:411px;font-size:10px">Adopt a Horse</div>
    <div class="abs d-small" style="left:140px;top:42px;width:131px;font-size:5px">Fernvale Quillstone is committed to helping match you with the perfect horse.</div>
    <div class="photo" role="img" aria-label="Photo of a bay horse in a field" style="left:52px;top:75px;width:98px;height:90px;background:linear-gradient(180deg,#cfd6e0 0%,#8fa08a 45%,#5a3a26 62%,#9aa378 100%)"></div>
    <div class="photo" role="img" aria-label="Photo of a bay horse standing in a paddock" style="left:156px;top:75px;width:98px;height:90px;background:linear-gradient(180deg,#cfd6e0 0%,#8fa08a 45%,#4a2e1e 62%,#9a9a88 100%)"></div>
    <div class="photo" role="img" aria-label="Photo of a chestnut horse on green grass" style="left:260px;top:75px;width:98px;height:90px;background:linear-gradient(180deg,#dfe6ea 0%,#b0b8a0 45%,#7a4a2a 62%,#6f9a3c 100%)"></div>
    <div class="btn" style="left:168px;top:185px;width:76px;font-size:4.5px;padding:2px 0">Adopt now</div>
  </section>
  <section class="abs" style="left:0;top:773px;width:411px;height:212px;background:#fff">
    <div class="photo" role="img" aria-label="Photo of a bay horse with a white blaze in a red halter" style="left:52px;top:22px;width:256px;height:175px;background:linear-gradient(180deg,#bfc7cf 0%,#6a4630 45%,#3a2416 75%,#8c7a66 100%)"></div>
    <div class="abs" style="left:205px;top:45px;width:150px;height:128px;background:var(--red)">
      <div class="serif-h" style="margin:22px 0 0 12px;font-size:9px">Horses</div>
      <div class="d-small" style="margin:2px 12px;font-size:4.5px">Many desktop publishing packages and web page editors now use Lorem Ipsum as their default model text, and a search for lorem ipsum.</div>
      <div class="btn" style="left:12px;top:70px;width:70px;font-size:4.5px;padding:2px 0">More ways to give</div>
    </div>
  </section>
  <section class="abs" style="left:0;top:985px;width:411px;height:163px;background:var(--red)">
    <div class="abs serif-h" style="left:0;top:20px;width:411px;text-align:center;font-size:9px">Have A Question Or Need More Information</div>
    <svg class="abs" style="left:54px;top:50px" width="16" height="16" viewBox="0 0 24 24"><circle cx="12" cy="12" r="11" fill="none" stroke="#fff" stroke-width="2"/><circle cx="12" cy="11" r="3" fill="#fff"/></svg>
    <div class="abs d-small" style="left:78px;top:50px;font-size:4.5px">LOCATION<br>Lorem Ipsum is simply<br>Dummy text P.O. Box 156</div>
    <svg class="abs" style="left:54px;top:84px" width="16" height="16" viewBox="0 0 24 24"><circle cx="12" cy="12" r="11" fill="none" stroke="#fff" stroke-width="2"/><circle cx="12" cy="12" r="3" fill="#fff"/></svg>
    <div class="abs d-small" style="left:78px;top:85px;font-size:4.5px">CALL US<br>123-456-789</div>
    <svg class="abs" style="left:54px;top:118px" width="16" height="16" viewBox="0 0 24 24"><circle cx="12" cy="12" r="11" fill="none" stroke="#fff" stroke-width="2"/><rect x="7" y="9" width="10" height="7" fill="#fff"/></svg>
    <div class="abs d-small" style="left:78px;top:119px;font-size:4.5px">MAIL US<br>fernvale@mail.com</div>
    <div class="d-field" style="left:182px;top:50px;width:86px">First Name</div>
    <div class="d-field" style="left:272px;top:50px;width:86px">Last Name</div>
    <div class="d-field" style="left:182px;top:66px;width:86px">Phone</div>
    <div class="d-field" style="left:272px;top:66px;width:86px">Email</div>
    <div class="d-field" style="left:182px;top:82px;width:176px;height:40px">How can we help you?</div>
    <div class="d-field" style="left:182px;top:128px;width:56px">Verify</div>
    <div class="btn" style="left:255px;top:128px;width:56px;font-size:4.5px;padding:3px 0">Submit now</div>
  </section>
  <footer class="abs" style="left:0;top:1148px;width:411px;height:142px;background:#000">
    <div class="brand abs" style="left:52px;top:42px;width:60px;text-align:center;font-size:7px">FERNVALE<br>QUILLSTONE<br>HERITAGE</div>
    <div class="abs d-small" style="left:137px;top:28px;font-size:4.5px;line-height:1.8">QUICK LINK<br>Home<br>About<br>Adopt<br>Horses<br>Donate / Shop<br>Contact</div>
    <div class="abs d-small" style="left:206px;top:28px;font-size:4.5px;line-height:1.8">QUICK CONTACT<br><span style="color:var(--red)">Location</span><br>Lorem Ipsum is simply<br>Dummy text<br>P.O. Box 156<br><span style="color:var(--red)">Location</span><br>P.O. Box 156</div>
    <div class="abs d-small" style="left:284px;top:28px;font-size:4.5px">FOLLOW US</div>
    <div class="abs d-small" style="left:284px;top:40px;width:74px;height:10px;background:#fff;color:#111;font-size:4px;text-align:center">Enter Your Mail ID</div>
    <div class="abs d-small" style="left:284px;top:53px;width:74px;height:10px;background:var(--red);font-size:4px;text-align:center">Subscribe</div>
    <svg class="abs" style="left:284px;top:68px" width="36" height="8" viewBox="0 0 36 8"><circle cx="4" cy="4" r="3.5" fill="#fff"/><circle cx="13" cy="4" r="3.5" fill="#fff"/><circle cx="22" cy="4" r="3.5" fill="#fff"/><circle cx="31" cy="4" r="3.5" fill="#fff"/></svg>
    <div class="abs d-small" style="left:0;top:126px;width:411px;text-align:center;font-size:4px;color:#888">Copyright 2021 Fernvale. All Right Reserved</div>
  </footer>
</main>

<div class="abs" style="left:420px;top:3330px;width:720px;text-align:center;font-family:var(--display);font-weight:700;font-size:56px">THANKS FOR WATCHING</div>

</body>
</html>
```